Help design website for "Brightwater Civic Advisors" to advance the common good

Here is the Google doc link that lays out the design:

https://files.plumrivet.example/sheet/d/7QmTzR2wLx9KpVbN4hJcY8sEaUoFdG3iXkMnPq5rWt6/edit?usp=sharing

Here is the Google drive folder with the logos and photos: https://vault.plumrivet.example/open?id=4HkWp9LzQe2TxRvN8mBaYc3DsUoJfG6

The testimonials are being gathered and will be shared by Friday, 1/4.

The winner will also have to migrate the coding files to my hosting site.

Thank you for your help! Looking forward to seeing your designs.

Target Market(s)

Prospective clients

Industry/Entity Type

Non Profit

Coding

Coded - Design and coding required

Number of Pages Required

5+ page

Requirements
Must have
• Noted in the Google doc regarding layout.
Nice to have

```html
<!DOCTYPE html>
<html lang="en">
<head>
<meta charset="utf-8">
<title>Brightwater Civic Advisors — Services &amp; Testimonials</title>
<link href="https://fonts.googleapis.com/css2?family=Poppins:wght@400;500;600;700&family=PT+Sans:wght@400;700&display=swap" rel="stylesheet">
<style>
  :root {
    --brand-blue: #3c8ad0;
    --ink: #2b2b2b;
    --body-text: #3a3a3a;
    --footer-bg: #25262e;
    --pattern-bg: #f1f2f4;
    --white: #ffffff;
    --muted: #d7d9de;
  }
  * { box-sizing: border-box; margin: 0; padding: 0; }
  html, body { width: 760px; height: 1200px; overflow: hidden; background: var(--white); }
  body { position: relative; font-family: "PT Sans", sans-serif; color: var(--body-text); }

  .site-header { position: absolute; left: 0; top: 0; width: 760px; height: 78px; background: var(--brand-blue); }
  .brand { position: absolute; display: flex; align-items: center; gap: 10px; }
  .brand-mark { width: 44px; height: 44px; background: var(--white); }
  .brand-name { font-family: "Poppins", sans-serif; font-weight: 500; color: var(--white); letter-spacing: 4px; line-height: 1.05; text-transform: uppercase; }
  .site-header .brand { left: 90px; top: 12px; }
  .site-header .brand-name { font-size: 14px; }
  .cta { position: absolute; left: 466px; top: 14px; width: 203px; height: 25px; border: 2px solid var(--white); color: var(--white); font-family: "Poppins", sans-serif; font-weight: 600; font-size: 8.6px; display: flex; align-items: center; justify-content: center; text-decoration: none; }
  .main-nav { position: absolute; top: 56px; right: 91px; display: flex; gap: 20px; }
  .main-nav a { font-family: "Poppins", sans-serif; font-weight: 600; font-size: 8.6px; color: var(--white); text-decoration: none; padding-bottom: 2px; }
  .main-nav a.active { border-bottom: 1px solid var(--white); }

  .hero { position: absolute; left: 0; top: 78px; width: 760px; height: 352px; background: linear-gradient(135deg, #c49a3a 0%, #7a5a2a 45%, #3a3236 70%, #6d6c70 100%); }
  .hero-edge { position: absolute; left: 0; top: 350px; width: 760px; height: 80px; }

  .intro { position: absolute; left: 0; top: 414px; width: 760px; text-align: center; }
  .intro h1 { font-family: "Poppins", sans-serif; font-weight: 600; font-size: 16.5px; color: var(--ink); }
  .intro p { width: 420px; margin: 16px auto 0; font-size: 10px; line-height: 13px; }

  .card { position: absolute; top: 531px; width: 278px; height: 416px; background: var(--white); box-shadow: 0 1px 6px rgba(0,0,0,.14); }
  .card-left { left: 90px; }
  .card-right { left: 390px; }
  .card-photo { position: relative; height: 226px; }
  .card-left .card-photo { background: linear-gradient(180deg, #8a8b8e 0%, #6b5a52 55%, #1c1c1e 100%); }
  .card-right .card-photo { background: linear-gradient(160deg, #2a2a2c 0%, #6a6c72 45%, #1a1a1c 100%); }
  .card-caption { position: absolute; left: 19px; bottom: 13px; right: 14px; font-family: "Poppins", sans-serif; font-weight: 700; font-size: 9.4px; line-height: 11.5px; color: var(--white); text-transform: uppercase; }
  .quote { position: relative; padding: 20px 18px 0 32px; font-size: 8.9px; line-height: 11.2px; color: var(--body-text); }
  .quote-mark { position: absolute; font-family: "Poppins", sans-serif; font-weight: 700; font-size: 24px; line-height: 1; color: var(--ink); }
  .quote-open { left: 17px; top: 16px; }
  .quote-close { position: relative; display: inline-block; font-family: "Poppins", sans-serif; font-weight: 700; font-size: 24px; line-height: 0; top: 9px; margin-left: 4px; color: var(--ink); }
  .attribution { padding: 0 18px 0 32px; font-size: 8.9px; line-height: 11.2px; }
  .attribution strong { font-weight: 700; color: var(--ink); }

  .pattern-band { position: absolute; left: 0; top: 948px; width: 760px; height: 120px; background: var(--pattern-bg); }
  .footer-shape { position: absolute; left: 0; top: 995px; width: 760px; height: 205px; }
  .site-footer { position: absolute; left: 0; top: 1065px; width: 760px; height: 135px; }
  .site-footer .brand { left: 90px; top: 18px; }
  .site-footer .brand-mark { width: 60px; height: 60px; background: var(--brand-blue); }
  .site-footer .brand-name { font-size: 18px; letter-spacing: 5px; }
  .footer-divider { position: absolute; left: 388px; top: 12px; width: 1px; height: 90px; background: #44464f; }
  .footer-menu { position: absolute; left: 426px; top: 26px; }
  .footer-menu h2 { font-family: "Poppins", sans-serif; font-weight: 700; font-size: 7.5px; color: var(--white); }
  .footer-menu nav { margin-top: 13px; display: flex; font-family: "Poppins", sans-serif; font-size: 7px; color: var(--muted); }
  .footer-menu nav a { color: var(--muted); text-decoration: none; }
  .footer-menu nav span { margin: 0 7px; }
  .copyright { position: absolute; left: 426px; top: 84px; font-family: "Poppins", sans-serif; font-size: 7px; color: var(--muted); }
</style>
</head>
<body>
  <header class="site-header">
    <div class="brand">
      <span class="brand-mark"></span>
      <span class="brand-name">Brightwater<br>Civic<br>Advisors</span>
    </div>
    <a class="cta" href="#">BOOK A COMPLIMENTARY CONSULTATION</a>
    <nav class="main-nav">
      <a href="#">ABOUT</a>
      <a href="#" class="active">SERVICES &amp; TESTIMONIALS</a>
      <a href="#">MEDIA &amp; IMPACT</a>
      <a href="#">CONTACT</a>
    </nav>
  </header>

  <div class="hero" role="img" aria-label="Group photo of the consultant with smiling workshop participants in a warm yellow room"></div>
  <svg class="hero-edge" viewBox="0 0 760 80" width="760" height="80" aria-hidden="true">
    <polygon points="0,66 382,6 760,74 760,80 0,80" fill="#3c8ad0"/>
    <polygon points="0,76 382,14 760,80 760,80 0,80" fill="#ffffff"/>
  </svg>

  <section class="intro">
    <h1>Group Facilitation &amp; Leadership Training</h1>
    <p>Nora has facilitated student groups, experiential learning activities, and dialogues on social justice issues, such as power and privilege, education, and poverty. She has developed curriculum and lesson plans for students to gain essential civic leadership competencies.</p>
  </section>

  <article class="card card-left">
    <div class="card-photo" role="img" aria-label="Nora speaking to a seated audience in an art gallery">
      <p class="card-caption">Nora providing context for a dialogue on arts and activism</p>
    </div>
    <span class="quote-mark quote-open" style="top:246px">&ldquo;</span>
    <p class="quote">Nora is one of the most talented and effective group facilitators I have ever worked with. It's obvious that she has years of experience designing and delivering dynamic, transformative trainings for groups from many different backgrounds, ages, and industries. She has the unique ability to not only provide new insight for her clients, but to engage and inspire her groups to continue their learning and growth long after her trainings. Nora is also an absolute blast to work with!<span class="quote-close">&rdquo;</span></p>
    <p class="attribution" style="margin-top:17px"><strong>Reed Callister,</strong> Chief Operations &amp; Growth Officer, Open Horizon Travel</p>
  </article>

  <article class="card card-right">
    <div class="card-photo" role="img" aria-label="Nora leading a discussion with high school students around a table">
      <p class="card-caption">Nora facilitating a college access workshop for high school students</p>
    </div>
    <span class="quote-mark quote-open" style="top:246px">&ldquo;</span>
    <p class="quote">In my 10 years in the education field across two different continents, I have never worked with such an incredible leader. Nora's calm but relentless disposition pushed our students to truly reflect and lead to unprecedented growth. Even as a fellow educator, I learned so much from Nora about myself and my craft. Her work is truly inspirational and life-changing.<span class="quote-close">&rdquo;</span></p>
    <p class="attribution" style="margin-top:30px"><strong>Dana Whitfield</strong> Dean of Culture, Lakeshore College Prep, Riverbend Network of Charter Schools</p>
  </article>

  <div class="pattern-band" role="img" aria-label="Faint light grey decorative band"></div>
  <svg class="footer-shape" viewBox="0 0 760 205" width="760" height="205" aria-hidden="true">
    <polygon points="0,70 380,0 760,70 760,205 0,205" fill="#25262e"/>
  </svg>

  <footer class="site-footer">
    <div class="brand">
      <span class="brand-mark"></span>
      <span class="brand-name">Brightwater<br>Civic<br>Advisors</span>
    </div>
    <div class="footer-divider"></div>
    <div class="footer-menu">
      <h2>MENU</h2>
      <nav>
        <a href="#">ABOUT</a><span>|</span>
        <a href="#">SERVICES &amp; TESTIMONIALS</a><span>|</span>
        <a href="#">MEDIA &amp; IMPACT</a><span>|</span>
        <a href="#">CONTACT</a>
      </nav>
    </div>
    <p class="copyright">Copyrights @ 2019 All Rights Reserved</p>
  </footer>
</body>
</html>
```